Nanny Share Ecommerce Website for Finding Childcare and Parents who need Childcare BrightPramHub.net

Our company needs an ecommerce website (BrightPramHub.net) for a US subscription based service strictly for nanny sharing that connects families and caregivers. The website would allow families to connect with one another as well as to search for nannies. The service would be searchable for other families by location (by radius or zip code), children demographic (age range/gender/special needs), days of week or times, after school care, school closure days (holidays), etc. The service would also be searchable for nannies based on gender, provider age range, years experience, language, hourly rate, transportation available, certification (CPR first aid), education etc. The search fields would be searchable and sortable and allow to connect with the provider (after paying subscription fee). The service would be similar to tendlyfolk.net in that it would allow for families and caregivers to post photos as well as a short bio of the themselves. There would also be a feedback/star rating mechanism to rate caregivers who have performed work for families (viewable to public). The service would be free for nannies to post their bios and only a subscription based service for families to connect with other families or with caregivers (able to view bio but need service to connect). There will be a short bio on the benefits of nanny sharing (reduced cost, increased flexibility for parents, reduced illness, increased socialization with other children vs. sole nanny), as well as Q&A section with best practices.

Target Market(s)

Families, Nannies

Industry/Entity Type

Childcare

Logo Text

Bright Pram Hub

Coding

Coded - Design and coding required

Number of Pages Required

5+ page

Requirements
Must have
• Searchable (need to be able to search for families as well as nannies), responsive, functional, easy to use, add value to families and nannies. Needs to be able to collect payment for subscription.
Nice to have
• Optimized for mobile, SEO optimized

```html
<!DOCTYPE html>
<html lang="en">
<head>
<meta charset="utf-8">
<title>Bright Pram Hub – Nanny Sharing</title>
<link href="https://fonts.googleapis.com/css2?family=Poppins:wght@300;400;500;600;700&display=swap" rel="stylesheet">
<style>
:root{
  --orange:#f15a24;
  --blue:#2fb3e3;
  --green:#8cc63f;
  --ink:#222;
  --text:#444;
  --muted:#777;
  --line:#e3e3e3;
  --dark:#3a3a3a;
  --foot:#f4f4f4;
}
*{box-sizing:border-box;margin:0;padding:0}
html,body{width:1200px;height:3529px;overflow:hidden}
body{font-family:"Poppins",sans-serif;color:var(--text);background:#fff;position:relative}
.abs{position:absolute}

/* header */
.site-header{position:absolute;left:0;top:0;width:1200px;height:118px;background:#fff}
.brand{position:absolute;left:100px;top:26px;display:flex;align-items:center;gap:12px}
.brand-dot{width:46px;height:46px;border-radius:50%;background:var(--orange)}
.brand-name{font-size:27px;font-weight:600;color:var(--green)}
.contact-top{position:absolute;right:98px;top:20px;display:flex;gap:34px;font-size:18px;color:#333}
.contact-top span{display:flex;align-items:center;gap:10px}
.main-nav{position:absolute;right:98px;top:72px;display:flex;gap:32px;font-size:15px;font-weight:500;color:#222}
.main-nav .active{color:var(--orange);position:relative}
.main-nav .active:after{content:"";position:absolute;left:0;right:0;bottom:-10px;height:2px;background:var(--orange)}

/* hero */
.hero{position:absolute;left:0;top:118px;width:1200px;height:630px}
.hero-photo{position:absolute;inset:0;background:linear-gradient(100deg,#6b5a4e 0%,#8d7666 30%,#c9a58a 55%,#e6cdb8 75%,#c4d8e0 100%)}
.hero-copy{position:absolute;left:94px;top:160px;width:420px;color:#fff}
.hero-copy h1{font-size:40px;font-weight:700;letter-spacing:.5px;margin-bottom:14px}
.hero-copy p{font-size:15px;line-height:26px;margin-bottom:24px}
.btn{display:inline-block;background:var(--orange);color:#fff;font-size:14px;font-weight:600;padding:10px 20px;border-radius:2px}
.hero-dots{position:absolute;left:98px;top:393px;display:flex;gap:6px}
.hero-dots i{width:12px;height:12px;border-radius:50%;border:2px solid #fff}
.hero-dots i:first-child{background:#fff}
.hero-ring{position:absolute;right:94px;top:494px;width:16px;height:16px;border-radius:50%;border:2px solid #fff}

/* seek boxes */
.seek{position:absolute;top:650px;width:500px;height:184px;display:flex;align-items:flex-start;padding:30px 28px 0 34px;gap:24px;color:#fff}
.seek.care{left:99px;background:var(--blue)}
.seek.nanny{left:599px;background:var(--green)}
.seek-icon{width:86px;height:86px;border-radius:50%;border:3px solid #fff;flex:none;display:flex;align-items:center;justify-content:center}
.seek h2{font-size:23px;font-weight:600;margin-bottom:6px;line-height:30px}
.seek p{font-size:13px;line-height:20px;margin-bottom:16px;width:320px}
.seek .btn{font-size:13px;padding:8px 16px}
.seek-shadow{position:absolute;left:99px;top:834px;width:1000px;height:40px;background:radial-gradient(ellipse at top,rgba(0,0,0,.18),transparent 70%)}

/* section titles */
.sec-title{position:absolute;left:0;width:1200px;text-align:center;font-size:34px;font-weight:500;color:var(--ink)}
.welcome-text{position:absolute;left:130px;top:976px;width:940px;text-align:center;font-size:13.5px;line-height:25px;color:#333}

/* services */
.services{position:absolute;left:99px;top:1219px;display:flex;gap:16px}
.service-card{width:238px;height:358px;background:#fff;box-shadow:0 2px 6px rgba(0,0,0,.15);position:relative;text-align:center}
.service-photo{height:170px}
.service-card .chip{position:absolute;left:99px;top:170px;width:40px;height:40px;border-radius:50%;background:var(--blue);border:3px solid #fff;display:flex;align-items:center;justify-content:center}
.service-card h3{margin-top:60px;font-size:19px;font-weight:500;color:var(--ink);line-height:26px}
.service-card p{margin:8px 14px 0;font-size:12.5px;line-height:23px;color:#444}

/* benefits */
.benefits{position:absolute;left:0;top:1678px;width:1200px;height:463px;background:linear-gradient(100deg,#8cc63f 0%,#63be8c 45%,#34b5dc 100%);color:#fff}
.benefits h2{position:absolute;top:76px;width:1200px;text-align:center;font-size:34px;font-weight:600}
.benefit-list{position:absolute;left:170px;top:186px;display:flex}
.benefit{width:220px;text-align:center}
.benefit-ring{width:112px;height:112px;margin:0 auto 20px;border:3px solid #fff;border-radius:50%;display:flex;align-items:center;justify-content:center}
.benefit p{font-size:17px;line-height:24px}

/* faq */
.col-title{position:absolute;top:2212px;font-size:29px;font-weight:500;color:var(--ink);letter-spacing:.5px}
.faq{position:absolute;left:99px;top:2294px;width:530px}
.faq-open-head{height:40px;background:var(--blue);color:#fff;font-size:15px;font-weight:500;display:flex;align-items:center;justify-content:space-between;padding-left:16px}
.faq-toggle{width:34px;height:40px;background:var(--dark);color:#fff;display:flex;align-items:center;justify-content:center;font-size:22px}
.faq-body{border:1px solid var(--line);border-top:0;padding:16px;font-size:13px;line-height:21px;color:#333;height:106px}
.faq-item{margin-top:12px;height:34px;border:1px solid var(--line);display:flex;align-items:center;justify-content:space-between;padding-left:16px;font-size:14px;color:#444}
.faq-item .faq-toggle{height:34px;width:30px;font-size:20px}
.video{position:absolute;left:697px;top:2294px;width:402px;height:311px;box-shadow:0 1px 4px rgba(0,0,0,.2)}
.video-frame{height:280px;background:linear-gradient(120deg,#e7d3c1,#c4a48c 50%,#9c8574)}
.play{position:absolute;left:176px;top:120px;width:50px;height:50px;border-radius:50%;border:3px solid #333;display:flex;align-items:center;justify-content:center}
.video-bar{height:31px;background:#f1f1f1;display:flex;align-items:center;gap:10px;padding:0 12px;font-size:10px;color:#555}
.video-bar .track{flex:1;height:4px;background:var(--orange)}
.video-bar .vol{width:48px;height:4px;background:var(--orange)}

/* reviews */
.reviews{position:absolute;left:0;top:2706px;width:1200px;height:424px;background:linear-gradient(180deg,#d4eeee,#f0f8f8)}
.reviews h2{position:absolute;top:70px;width:1200px;text-align:center;font-size:30px;font-weight:500;color:var(--ink)}
.reviews .rule{position:absolute;left:570px;top:122px;width:60px;height:3px;background:var(--blue)}
.review{position:absolute;top:184px;width:470px;display:flex;gap:24px}
.avatar{width:122px;height:122px;border-radius:50%;flex:none;background:linear-gradient(135deg,#e9c9a8,#b58a6a)}
.review p{font-size:13px;line-height:21px;color:#333}
.review .who{margin-top:12px;font-size:12.5px;font-weight:500;color:#222}
.stars{color:var(--orange);font-size:14px;letter-spacing:3px;margin-top:6px}

/* footer */
.site-footer{position:absolute;left:0;top:3130px;width:1200px;height:329px;background:var(--foot)}
.foot-brand{position:absolute;left:100px;top:80px;text-align:center}
.foot-brand .brand-dot{margin:0 auto 12px;width:64px;height:64px}
.foot-brand .brand-name{font-size:26px}
.socials{display:flex;gap:6px;justify-content:center;margin-top:14px}
.socials i{width:22px;height:22px;border-radius:50%;border:1px solid #555}
.foot-col{position:absolute;top:70px}
.foot-col h4{font-size:19px;font-weight:600;color:var(--ink);letter-spacing:.5px;margin-bottom:20px}
.foot-contact li{list-style:none;display:flex;gap:14px;font-size:13px;line-height:20px;color:#333;margin-bottom:16px}
.foot-links li{list-style:none;font-size:12.5px;line-height:24px;color:#333}
.foot-links li:before{content:"▸";font-size:10px;margin-right:10px}
.newsletter p{font-size:12.5px;line-height:20px;color:#555;width:290px}
.newsletter .field{margin-top:16px;width:296px;height:42px;background:#fff;border:1px solid var(--line);font-size:12px;color:#777;padding:12px}
.newsletter .btn{margin-top:16px;padding:9px 30px}
.copyright{position:absolute;left:0;top:3459px;width:1200px;height:70px;border-top:1px solid var(--line);text-align:center;font-size:13px;color:#444;line-height:70px;background:#fff}
</style>
</head>
<body>

<header class="site-header">
  <div class="brand"><span class="brand-dot"></span><span class="brand-name">Bright Pram Hub</span></div>
  <div class="contact-top">
    <span><svg width="26" height="26" viewBox="0 0 26 26"><circle cx="13" cy="13" r="12" fill="none" stroke="#2fb3e3" stroke-width="1.5"/><path d="M9 7l3 3-1.5 2a8 8 0 0 0 3.5 3.5l2-1.5 3 3-2 2c-5 0-10-5-10-10z" fill="#2fb3e3"/></svg>+(08) 5550 1482</span>
    <span><svg width="26" height="26" viewBox="0 0 26 26"><circle cx="13" cy="13" r="12" fill="none" stroke="#2fb3e3" stroke-width="1.5"/><rect x="7" y="9" width="12" height="8" fill="none" stroke="#2fb3e3" stroke-width="1.5"/><path d="M7 9l6 5 6-5" fill="none" stroke="#2fb3e3" stroke-width="1.5"/></svg>info@brightpramhub.net</span>
  </div>
  <nav class="main-nav">
    <span class="active">HOME</span><span>ABOUT US</span><span>OUR SERVICES</span><span>FAQ</span><span>BLOG</span><span>CONTACT</span>
  </nav>
</header>

<section class="hero">
  <div class="hero-photo" role="img" aria-label="Photo of a smiling mother hugging her young daughter at home"></div>
  <div class="hero-copy">
    <h1>BRIGHT PRAM HUB</h1>
    <p>Sed ut perspiciatis unde omnis iste natus error sit voluptatem accusantium doloremque laudatium, totam rem aperiam, eaque ipsa quae</p>
    <span class="btn">READ MORE</span>
  </div>
  <div class="hero-dots"><i></i><i></i><i></i></div>
  <div class="hero-ring"></div>
</section>

<div class="seek care">
  <div class="seek-icon"><svg width="44" height="44" viewBox="0 0 44 44" fill="#fff"><circle cx="22" cy="8" r="5"/><path d="M10 16h24v4h-8v20h-4v-10h-0v10h-4V20h-8z"/></svg></div>
  <div><h2>I NEED A CAREGIVER</h2><p>Lorem ipsum dolor sit amet, consectetur ascing elit, sed do eiusmod tempor incididunt</p><span class="btn">FIND CARE</span></div>
</div>
<div class="seek nanny">
  <div class="seek-icon"><svg width="44" height="44" viewBox="0 0 44 44" fill="#fff"><circle cx="17" cy="8" r="5"/><path d="M12 15h10v12h-10zM14 27h4v12h-4z"/><circle cx="32" cy="22" r="4"/><path d="M28 28h8v8h-8z"/></svg></div>
  <div><h2>I WANT A CARE NANNY</h2><p>Lorem ipsum dolor sit amet, consectetur ascing elit, sed do eiusmod tempor incididunt</p><span class="btn">SEARCH FOR NANNY</span></div>
</div>
<div class="seek-shadow"></div>

<h2 class="sec-title" style="top:910px">WELCOME TO BRIGHT PRAM HUB</h2>
<p class="welcome-text">Sed ut perspiciatis unde omnis iste natus error sit voluptatem accusantium doloremque laudantium, totam rem aperiam, eaque ipsa quae ab illo inventore veritatis et quasi architecto beatae vitae dicta sunt explicabo. Nemo enim ipsam voluptatem quia voluptas sit aspernatur aut odit aut fugit, sed quia consequuntur magni dolores eos qui ratione voluptatem sequi nesciunt. Neque porro quisquam est, qui dolorem ipsum quia dolor sit amet, consectetur, adipisci velit, sed quia non numquam eius modi tempora incidunt ut labore</p>

<h2 class="sec-title" style="top:1137px">OUR SERVICES</h2>
<div class="services">
  <article class="service-card">
    <div class="service-photo" role="img" aria-label="Photo of children playing with building blocks" style="background:linear-gradient(135deg,#f2c46a,#d9775a 60%,#8fb9d8)"></div>
    <span class="chip"><svg width="18" height="18" viewBox="0 0 18 18" fill="#fff"><circle cx="9" cy="4" r="3"/><path d="M5 8h8l-1 9H6z"/></svg></span>
    <h3>Child care</h3><p>Sed ut perspiciatis unde omnis iste natus error sit voluptatem santium doloremque laudantium</p>
  </article>
  <article class="service-card">
    <div class="service-photo" role="img" aria-label="Photo of a carer with a senior woman" style="background:linear-gradient(135deg,#c9d6de,#e6cbb5 55%,#5aa2c9)"></div>
    <span class="chip"><svg width="18" height="18" viewBox="0 0 18 18" fill="#fff"><circle cx="6" cy="4" r="2.5"/><circle cx="12" cy="4" r="2.5"/><path d="M3 8h6v9H3zM10 8h5v9h-5z"/></svg></span>
    <h3>Adult &amp; senior care</h3><p>Sed ut perspiciatis unde omnis iste natus error sit voluptatem santium doloremque laudantium</p>
  </article>
  <article class="service-card">
    <div class="service-photo" role="img" aria-label="Photo of a woman cuddling her dog" style="background:linear-gradient(135deg,#6b6f73,#b08a6a 55%,#d9c2a8)"></div>
    <span class="chip"><svg width="18" height="18" viewBox="0 0 18 18" fill="#fff"><circle cx="5" cy="5" r="2"/><circle cx="13" cy="5" r="2"/><circle cx="3" cy="10" r="2"/><circle cx="15" cy="10" r="2"/><ellipse cx="9" cy="13" rx="4" ry="3"/></svg></span>
    <h3>Pet care</h3><p>Sed ut perspiciatis unde omnis iste natus error sit voluptatem santium doloremque laudantium</p>
  </article>
  <article class="service-card">
    <div class="service-photo" role="img" aria-label="Photo of a carer visiting an elderly man at home" style="background:linear-gradient(135deg,#eef1f0,#d9c7b3 55%,#a2b58a)"></div>
    <span class="chip"><svg width="18" height="18" viewBox="0 0 18 18" fill="#fff"><path d="M9 2l7 7h-2v7H4V9H2z"/></svg></span>
    <h3>Home care</h3><p>Sed ut perspiciatis unde omnis iste natus error sit voluptatem santium doloremque laudantium</p>
  </article>
</div>

<section class="benefits">
  <h2>THE BENEFITS OF NANNY SHARING</h2>
  <div class="benefit-list">
    <div class="benefit"><div class="benefit-ring"><svg width="60" height="50" viewBox="0 0 60 50"><text x="30" y="34" text-anchor="middle" font-family="Poppins,sans-serif" font-size="30" font-weight="600" fill="#fff">$$$</text><path d="M30 38v10M26 44l4 4 4-4" stroke="#fff" stroke-width="2" fill="none"/></svg></div><p>Reduced Cost</p></div>
    <div class="benefit"><div class="benefit-ring"><svg width="56" height="56" viewBox="0 0 56 56" fill="#fff"><circle cx="18" cy="12" r="6"/><circle cx="38" cy="12" r="6"/><path d="M10 22h16v16h-3v14h-10V38h-3zM30 22h16l3 16h-5v14h-10V38h-4z"/></svg></div><p>Increased Flexibility<br>For Parents</p></div>
    <div class="benefit"><div class="benefit-ring"><svg width="56" height="56" viewBox="0 0 56 56"><circle cx="28" cy="12" r="7" fill="#fff"/><path d="M14 34c0-8 6-14 14-14s14 6 14 14" fill="none" stroke="#fff" stroke-width="3"/><circle cx="28" cy="40" r="8" fill="none" stroke="#fff" stroke-width="3"/><path d="M24 40h8" stroke="#fff" stroke-width="3"/></svg></div><p>Reduced Illness</p></div>
    <div class="benefit"><div class="benefit-ring"><svg width="56" height="56" viewBox="0 0 56 56" fill="#fff"><circle cx="17" cy="14" r="7"/><circle cx="39" cy="14" r="7"/><path d="M9 24h16l3 16h-6v12h-8V40H8zM31 24h16v16h-4v12h-8V40h-4z"/></svg></div><p>Increased Socialization<br>With Other Children Vs.<br>Sole Nanny</p></div>
  </div>
</section>

<h2 class="col-title" style="left:99px">FAQ</h2>
<h2 class="col-title" style="left:697px">NANNY TAXES MADE EASY</h2>
<div class="faq">
  <div class="faq-open-head">Why do we use it?<span class="faq-toggle">−</span></div>
  <div class="faq-body">Lorem ipsum dolor sit amet, consectetur adipiscing elit, sed do eiusmod tempor incididunt ut labore et dolore magna aliqua. Ut enim ad minim veniam, quis nostrud exercitation ullamco laboris</div>
  <div class="faq-item">Where can I get some?<span class="faq-toggle">+</span></div>
  <div class="faq-item">Where does it come from?<span class="faq-toggle">+</span></div>
  <div class="faq-item">Where can I get some?<span class="faq-toggle">+</span></div>
  <div class="faq-item">Where does it come from?<span class="faq-toggle">+</span></div>
</div>
<div class="video">
  <div class="video-frame" role="img" aria-label="Video still of two women reviewing paperwork on a tablet"></div>
  <span class="play"><svg width="18" height="20" viewBox="0 0 18 20"><path d="M2 1l15 9-15 9z" fill="#333"/></svg></span>
  <div class="video-bar"><span>▶</span><span>00:00</span><span class="track"></span><span>◀)</span><span class="vol"></span></div>
</div>

<section class="reviews">
  <h2>CUSTOMER REVIEWS</h2>
  <span class="rule"></span>
  <div class="review" style="left:99px">
    <div class="avatar" role="img" aria-label="Portrait photo of a reviewer with her child"></div>
    <div><p>“ Nemo enim ipsam voluptatem quia voluptas sit aspernatur aut odit aut fugit, sed quia consequuntur magni dolores eos qui ratione voluptatem</p><div class="who">JOHN DOE – BRIGHT PRAM HUB</div><div class="stars">★★★★★</div></div>
  </div>
  <div class="review" style="left:637px">
    <div class="avatar" role="img" aria-label="Portrait photo of a reviewer reading with a child" style="background:linear-gradient(135deg,#c9e0ea,#e0b48e)"></div>
    <div><p>“ Nemo enim ipsam voluptatem quia voluptas sit aspernatur aut odit aut fugit, sed quia consequuntur magni dolores eos qui ratione voluptatem</p><div class="who">JOHN DOE – BRIGHT PRAM HUB</div><div class="stars">★★★★★</div></div>
  </div>
  <svg class="abs" style="left:0;top:350px" width="1200" height="74" viewBox="0 0 1200 74" preserveAspectRatio="none">
    <path d="M0 30C250 -10 450 70 700 40S1050 10 1200 30V74H0z" fill="#f4f4f4"/>
    <path d="M0 30C250 -10 450 70 700 40S1050 10 1200 30" fill="none" stroke="#2fb3e3" stroke-width="5"/>
    <path d="M0 42C260 6 460 78 700 52S1060 24 1200 42" fill="none" stroke="#8cc63f" stroke-width="4"/>
  </svg>
</section>

<footer class="site-footer">
  <div class="foot-brand">
    <div class="brand-dot"></div>
    <div class="brand-name">Bright Pram Hub</div>
    <div class="socials"><i></i><i></i><i></i><i></i></div>
  </div>
  <div class="foot-col" style="left:320px">
    <h4>CONTACT US</h4>
    <ul class="foot-contact">
      <li><svg width="14" height="18" viewBox="0 0 14 18"><path d="M7 0a7 7 0 0 0-7 7c0 5 7 11 7 11s7-6 7-11a7 7 0 0 0-7-7z" fill="#333"/><circle cx="7" cy="7" r="2.5" fill="#f4f4f4"/></svg><span>58 Bright Pram Lane, Suite 14<br>Maple Hollow, ST 00000</span></li>
      <li><svg width="14" height="16" viewBox="0 0 14 16"><path d="M2 1l3 3-1.5 2.5a8 8 0 0 0 4 4L10 9l3 3-2 3C6 15 0 9 0 3z" fill="#333"/></svg><span>Phone: 800-555-0142</span></li>
      <li><svg width="14" height="12" viewBox="0 0 14 12"><rect width="14" height="12" fill="#333"/><path d="M0 0l7 6 7-6" fill="none" stroke="#f4f4f4"/></svg><span>info@brightpramhub.net</span></li>
    </ul>
  </div>
  <div class="foot-col" style="left:603px">
    <h4>QUICK LINKS</h4>
    <ul class="foot-links"><li>Home</li><li>About Us</li><li>Find Home Care</li><li>Types of Care</li><li>Blog</li><li>FAQs</li><li>Contact</li></ul>
  </div>
  <div class="foot-col newsletter" style="left:803px">
    <h4>SIGN UP FOR NEWSLETTER</h4>
    <p>Excepteur sint occaecat cupidatat non proident, sunt in culpa qui officia deserunt</p>
    <div class="field">Enter email</div>
    <span class="btn">SIGN UP</span>
  </div>
</footer>
<div class="copyright">© Copyright 2018 Bright Pram Hub. All Rights Reserved.</div>

</body>
</html>
```